Larkspur Talent IT Recruiting firm needs a business card design for Recruiters, Sourcers, and Account

We need business cards that allow us to change all contact info, names, titles (Recruiter, Sourcer, Account Manager, Director, CEO, etc) per person since we have three offices, in three cities, Phoenix, Austin, and Las Vegas. We do recruiting and contractors for IT positions (Developers, Architects, Software Engineers, Security Engineers, Help Desk, DBAs, PMs, Scrum Masters, etc.) Our client companies are very diverse from Meridian 100 to silicone Valley type start-ups.

So, while we what hip, techie, and quirky, it still needs to be professional. Primary color we use is blue, with silver as a secondary color.

Target Market(s)

IT, Technology

Industry/Entity Type

Business

Contact Information for Business Card

Company name: Larkspur Talent, Inc.
Website: www.larkspurtalent.example
Logos for Careerloop, Blipster, and Myriada

Name, Title, Office Number, Cell Number, email

Font styles to use
Serif
Sans Serif

Colors
0455a3
d5d5d5

Requirements
Nice to have
• The grey I selected below is not necessary - but, would like silver included. I included a card design (File 3: LTI early trial example.jpg) that I had started on. It's very rough, and not quite what we're looking for, but what we did like is the logo, big, maybe a bit faded, off center, goes out of frame, etc. Still looking for other ideas - you are the pros! But, just an idea of a design element we liked.

```html
<!DOCTYPE html>
<html lang="en">
<head>
<meta charset="utf-8">
<title>Larkspur Talent — Business Card</title>
<link rel="stylesheet" href="https://fonts.googleapis.com/css2?family=Cinzel:wght@400;600&family=Lato:wght@400;700&display=swap">
<style>
  :root {
    --page-bg: #e9ebee;
    --blue-light: #3db8f5;
    --blue-mid: #1f86ee;
    --blue-deep: #0a48e0;
    --brand-blue: #0455a3;
    --accent-blue: #2a93ee;
    --ink: #1b1b1b;
    --ink-soft: #3a3a3a;
    --card-white: #ffffff;
    --card-silver: #e6e7e9;
    --white: #ffffff;
  }
  * { margin: 0; padding: 0; box-sizing: border-box; }
  html, body {
    width: 1200px; height: 900px; overflow: hidden;
    background: var(--page-bg);
  }
  .canvas { position: relative; width: 1200px; height: 900px; }

  .card {
    position: absolute; width: 630px; height: 360px;
    overflow: hidden; border-radius: 4px;
    box-shadow: 0 10px 26px rgba(0,0,0,.18);
  }

  /* Back of card */
  .card-back {
    left: 110px; top: 100px;
    background: linear-gradient(180deg, var(--blue-light) 0%, var(--blue-mid) 50%, var(--blue-deep) 100%);
    color: var(--white); text-align: center;
  }
  .back-mark {
    position: absolute; left: 50%; top: 78px; transform: translateX(-50%);
    display: flex; align-items: center; gap: 14px;
  }
  .back-mark .dot { width: 22px; height: 22px; border-radius: 50%; background: var(--white); }
  .back-mark .wordmark {
    font-family: "Cinzel", serif; font-weight: 600; font-size: 40px;
    letter-spacing: 3px; color: var(--white); white-space: nowrap;
  }
  .back-url {
    position: absolute; left: 0; right: 0; top: 208px;
    font-family: "Lato", sans-serif; font-size: 19px; letter-spacing: .5px;
  }
  .social-list {
    position: absolute; left: 0; right: 0; top: 248px;
    display: flex; justify-content: center; gap: 18px; list-style: none;
    font-family: "Lato", sans-serif; font-size: 13px;
  }
  .social-list li { display: flex; align-items: center; gap: 6px; }
  .social-list .dot { width: 12px; height: 12px; border-radius: 50%; background: var(--white); }

  /* Front of card */
  .card-front {
    left: 470px; top: 440px;
    background: radial-gradient(ellipse at 30% 40%, var(--card-white) 0%, var(--card-white) 45%, var(--card-silver) 100%);
  }
  .front-decor { position: absolute; right: -120px; top: -60px; width: 360px; height: 420px; }

  .front-logo {
    position: absolute; left: 40px; top: 62px;
    font-family: "Cinzel", serif; font-weight: 400; color: var(--ink);
  }
  .front-logo .line-1 { font-size: 50px; letter-spacing: 4px; line-height: 1; display: block; }
  .front-logo .line-2 { font-size: 26px; letter-spacing: 6px; line-height: 1.1; display: block; text-align: right; }
  .tagline {
    position: absolute; left: 40px; top: 172px;
    font-family: "Cinzel", serif; font-size: 15px; letter-spacing: 2.5px; color: var(--ink-soft);
  }

  .contact {
    position: absolute; right: 230px; top: 200px; text-align: right;
    font-family: "Lato", sans-serif; color: var(--ink);
  }
  .contact .person-name { font-size: 22px; font-weight: 700; color: var(--accent-blue); }
  .contact .person-title { font-size: 16px; margin-top: 2px; }
  .contact-lines { list-style: none; margin-top: 18px; font-size: 17px; line-height: 1.35; }
  .contact-lines li { display: flex; justify-content: flex-end; align-items: center; gap: 6px; }
  .contact-lines svg { width: 12px; height: 12px; flex: none; }
</style>
</head>
<body>
<main class="canvas">

  <section class="card card-back" aria-label="Card back">
    <div class="back-mark">
      <span class="dot"></span>
      <span class="wordmark">Larkspur Talent</span>
    </div>
    <p class="back-url">www.larkspurtalent.example</p>
    <ul class="social-list">
      <li><span class="dot"></span>Myriada</li>
      <li><span class="dot"></span>Blipster</li>
      <li><span class="dot"></span>Careerloop</li>
    </ul>
  </section>

  <section class="card card-front" aria-label="Card front">
    <svg class="front-decor" viewBox="0 0 360 420" role="img" aria-label="Large faded brand mark decoration, going off the card edge">
      <defs>
        <linearGradient id="decorFill" x1="0" y1="0" x2="0" y2="1">
          <stop offset="0" stop-color="#3db8f5"/>
          <stop offset="1" stop-color="#0a48e0"/>
        </linearGradient>
      </defs>
      <circle cx="230" cy="200" r="210" fill="url(#decorFill)"/>
    </svg>

    <div class="front-logo">
      <span class="line-1">LARKSPUR</span>
      <span class="line-2">TALENT</span>
    </div>
    <p class="tagline">RISING TO THE CHALLENGE</p>

    <div class="contact">
      <p class="person-name">Dana Whitfield R</p>
      <p class="person-title">Designation</p>
      <ul class="contact-lines">
        <li>555 014-2290
          <svg viewBox="0 0 12 12" aria-hidden="true"><path d="M2 3c0-1 1-1.5 4-1.5S10 2 10 3v1H8V3H4v1H2zM3 5h6l1 5H2z" fill="var(--accent-blue)"/></svg>
        </li>
        <li>555 014-2290
          <svg viewBox="0 0 12 12" aria-hidden="true"><rect x="3" y="0.8" width="6" height="10.4" rx="1.2" fill="none" stroke="var(--accent-blue)" stroke-width="1.4"/></svg>
        </li>
        <li>info@larkspurtalent.example
          <svg viewBox="0 0 12 12" aria-hidden="true"><rect x="0.5" y="2" width="11" height="8" fill="var(--accent-blue)"/><path d="M1 2.5l5 4 5-4" fill="none" stroke="#fff" stroke-width="1"/></svg>
        </li>
      </ul>
    </div>
  </section>

</main>
</body>
</html>
```